landscaping core flute signs

I need core flutes created with business name and a few extra dot points for putting on fences for job sites 120cm x 120cm approx.
I want our old ones information with the new L logo and colour palette

```html
<!DOCTYPE html>
<html lang="en">
<head>
<meta charset="utf-8">
<title>Terrace Ground – Site Sign</title>
<link rel="stylesheet" href="https://fonts.googleapis.com/css2?family=Cinzel:wght@500&family=Arimo:wght@400;700&family=Roboto+Condensed:wght@700&family=Montserrat:wght@700&display=swap">
<style>
  :root {
    --backdrop: #9a9a9a;
    --sign-black: #000000;
    --leaf-green: #5f8a58;
    --white: #ffffff;
  }
  * { margin: 0; padding: 0; box-sizing: border-box; }
  html, body {
    width: 1200px;
    height: 829px;
    overflow: hidden;
    background: var(--backdrop);
  }
  .canvas {
    position: relative;
    width: 1200px;
    height: 829px;
  }
  .sign {
    position: absolute;
    left: 282px;
    top: 96px;
    width: 637px;
    height: 637px;
    background: var(--sign-black);
    color: var(--white);
    overflow: hidden;
  }
  .brand-mark {
    position: absolute;
    left: 238px;
    top: 38px;
    width: 160px;
    height: 160px;
    border-radius: 50%;
    background: var(--leaf-green);
  }
  .brand-name {
    position: absolute;
    top: 218px;
    left: 0;
    width: 100%;
    text-align: center;
    font-family: "Cinzel", serif;
    font-weight: 500;
    font-size: 36px;
    letter-spacing: 1px;
    color: var(--white);
  }
  .tagline {
    position: absolute;
    top: 288px;
    left: 0;
    width: 100%;
    text-align: center;
    font-family: "Cinzel", serif;
    font-weight: 500;
    font-size: 12px;
    letter-spacing: 4.6px;
    color: var(--leaf-green);
  }
  .services {
    position: absolute;
    top: 322px;
    left: 180px;
    list-style: none;
  }
  .service {
    display: flex;
    align-items: center;
    height: 50px;
    font-family: "Arimo", sans-serif;
    font-size: 26px;
    color: var(--white);
  }
  .service-dot {
    width: 24px;
    height: 24px;
    border-radius: 50%;
    background: var(--leaf-green);
    margin-right: 13px;
    flex: none;
  }
  .phone {
    position: absolute;
    top: 460px;
    left: 0;
    width: 100%;
    text-align: center;
    font-family: "Roboto Condensed", sans-serif;
    font-weight: 700;
    font-size: 62px;
    line-height: 1;
    color: var(--white);
  }
  .email {
    position: absolute;
    top: 533px;
    left: 0;
    width: 100%;
    text-align: center;
    font-family: "Arimo", sans-serif;
    font-weight: 700;
    font-size: 27px;
    color: var(--white);
  }
  .footer-band {
    position: absolute;
    left: 0;
    top: 592px;
    width: 637px;
    height: 45px;
  }
  .licence {
    position: absolute;
    left: 427px;
    top: 597px;
    font-family: "Montserrat", sans-serif;
    font-weight: 700;
    font-size: 18px;
    letter-spacing: 0.5px;
    color: var(--white);
  }
</style>
</head>
<body>
  <main class="canvas">
    <section class="sign">
      <div class="brand-mark" aria-hidden="true"></div>
      <h1 class="brand-name">TERRACE GROUND</h1>
      <p class="tagline">STRUCTURAL LANDSCAPING</p>

      <ul class="services">
        <li class="service"><span class="service-dot"></span>Paving &amp; Concreting</li>
        <li class="service"><span class="service-dot"></span>Fencing &amp; Retaining</li>
        <li class="service"><span class="service-dot"></span>Desgin &amp; Construct</li>
      </ul>

      <p class="phone">0491 570 156</p>
      <p class="email">sam@terraceground.com</p>

      <svg class="footer-band" viewBox="0 0 637 45" aria-hidden="true">
        <path d="M0,19 L388,19 C398,19 404,0 420,0 L637,0 L637,45 L0,45 Z" fill="var(--leaf-green)"/>
        <path d="M0,6 L392,6 C400,6 402,11 410,11 L410,14 C400,14 398,9 392,9 L0,9 Z" fill="var(--white)"/>
      </svg>
      <p class="licence">QBSA:&nbsp; 1098734</p>
    </section>
  </main>
</body>
</html>
```